Verodex business card

Business card for sustainable investment company called "Verodex". Verodex is an exchange platform selling carbon credits between buyers and sellers. Carbon Credits are an environmental commodity for reducing global carbon emissions.

the card should obviously have our logo and the theme should be sustainability/environment mixed with a trading platform.

Contact Information for Business Card

Logo, Name, Title, Phone, Email

Colors
0054AA
0677BA
7BADD7
CADEEF
E8F1F8
0094D4
00A9DD
6FCCEA
C7EBF8
E9F6FB
00AB8E
00BBA5
67D7C9
C6EFE9
E9F9F6
59FF00
82FF00
B8FF75
E3FFCB
F4FFEA

```html
<!DOCTYPE html>
<html lang="en">
<head>
<meta charset="utf-8">
<title>Verodex business card</title>
<link rel="stylesheet" href="https://fonts.googleapis.com/css2?family=Montserrat:wght@700&family=Open+Sans:wght@400;600;700&display=swap">
<style>
  :root {
    --backdrop: #1b1e24;
    --navy: #132a52;
    --navy-edge: #0f2246;
    --aqua: #67cddb;
    --azure: #4f7fc8;
    --name-blue: #4da3d8;
    --white: #ffffff;
  }
  * { box-sizing: border-box; margin: 0; padding: 0; }
  html, body { width: 1200px; height: 780px; overflow: hidden; }
  body {
    background: var(--backdrop);
    font-family: "Open Sans", Arial, sans-serif;
    position: relative;
  }
  .card {
    position: absolute;
    top: 232px;
    width: 540px;
    height: 316px;
    background: var(--navy);
    overflow: hidden;
    box-shadow: 0 0 0 1px var(--navy-edge);
  }
  .card--front { left: 40px; }
  .card--back { left: 620px; }

  .wordmark {
    font-family: "Montserrat", Arial, sans-serif;
    font-weight: 700;
    color: var(--white);
    letter-spacing: 0.02em;
    display: flex;
    align-items: center;
    gap: 10px;
    text-transform: uppercase;
  }
  .wordmark__dot {
    width: 14px; height: 14px;
    background: var(--aqua);
    border-radius: 50%;
  }
  .card--front .wordmark {
    position: absolute;
    left: 34px; top: 38px;
    font-size: 30px;
  }
  .card--back .wordmark {
    position: absolute;
    left: 0; right: 0; top: 0; bottom: 0;
    justify-content: center;
    font-size: 52px;
  }
  .card--back .wordmark__dot { width: 22px; height: 22px; }

  .holder {
    position: absolute;
    right: 30px; top: 94px;
    text-align: right;
  }
  .holder__name {
    font-weight: 700;
    font-size: 27px;
    color: var(--name-blue);
    line-height: 1.1;
  }
  .holder__title {
    font-size: 15px;
    color: var(--white);
    margin-top: 3px;
  }

  .accent-tab {
    position: absolute;
    right: 0; top: 150px;
    width: 14px; height: 40px;
    background: linear-gradient(180deg, var(--aqua), var(--azure));
  }

  .contact-panel {
    position: absolute;
    left: 0; top: 126px;
    width: 350px; height: 190px;
    background: linear-gradient(160deg, var(--aqua), var(--azure));
    clip-path: polygon(0 0, 100% 0, 74% 100%, 0 100%);
  }
  .contact {
    position: absolute;
    left: 26px; top: 140px;
    list-style: none;
    color: var(--white);
    font-size: 13.5px;
    line-height: 1.32;
  }
  .contact__address { margin-bottom: 6px; }
  .contact__row { display: flex; align-items: center; gap: 7px; }
  .contact__row svg { width: 13px; height: 13px; flex: none; }
</style>
</head>
<body>
  <section class="card card--front" aria-label="Business card front">
    <div class="contact-panel"></div>
    <div class="wordmark"><span class="wordmark__dot"></span>Verodex</div>
    <div class="holder">
      <p class="holder__name">Marta Kollarova</p>
      <p class="holder__title">Managing Director</p>
    </div>
    <div class="accent-tab"></div>
    <ul class="contact">
      <li class="contact__address">214 Linden Park Rd Austin,<br>Texas 78701 USA</li>
      <li class="contact__row">
        <svg viewBox="0 0 24 24" aria-hidden="true"><path fill="#fff" d="M6.6 10.8a15.1 15.1 0 0 0 6.6 6.6l2.2-2.2a1 1 0 0 1 1-.25 11.4 11.4 0 0 0 3.6.57 1 1 0 0 1 1 1V20a1 1 0 0 1-1 1A17 17 0 0 1 3 4a1 1 0 0 1 1-1h3.5a1 1 0 0 1 1 1c0 1.25.2 2.45.57 3.57a1 1 0 0 1-.25 1z"/></svg>
        (512) 555-0147
      </li>
      <li class="contact__row">
        <svg viewBox="0 0 24 24" aria-hidden="true"><rect x="2" y="5" width="20" height="14" rx="2" fill="none" stroke="#fff" stroke-width="2"/><path d="M3 6l9 7 9-7" fill="none" stroke="#fff" stroke-width="2"/></svg>
        hello@verodex-mail.com
      </li>
      <li class="contact__row">
        <svg viewBox="0 0 24 24" aria-hidden="true"><circle cx="12" cy="12" r="9.5" fill="none" stroke="#fff" stroke-width="2"/><path d="M2.5 12h19M12 2.5c3 3 3 16 0 19M12 2.5c-3 3-3 16 0 19" fill="none" stroke="#fff" stroke-width="1.6"/></svg>
        www.verodex-trade.com
      </li>
    </ul>
  </section>

  <section class="card card--back" aria-label="Business card back">
    <div class="wordmark"><span class="wordmark__dot"></span>Verodex</div>
  </section>
</body>
</html>
```